Personal training and nutrition business needs business card design

We need a business card that outlays our services and invites potential customers to join our team and take the first step to a healthier and more enjoyable life. We cater for any level of fitness and specialize in weight loss and conditioning, strength training, muscle gain and strength endurance. Whether you are just starting off or need some help getting to the next level of your journey we are here to get the job done.
We specialize in one on one or one on two personal training sessions and each program will be custom made to suit individual fitness goals of our clients

```html
<!DOCTYPE html>
<html lang="en">
<head>
<meta charset="utf-8">
<title>Stride &amp; Tempo – Business Card</title>
<link rel="stylesheet" href="https://fonts.googleapis.com/css2?family=Roboto:ital,wght@0,400;0,500;0,700;0,900;1,900&display=swap">
<style>
  :root {
    --backdrop: #2b2b2b;
    --violet-deep: #553683;
    --violet-mid: #7a4894;
    --orchid: #9d56a2;
    --ink: #1f1f22;
    --ink-soft: #333338;
    --paper: #f1f1f1;
    --tag-light: #ece4f3;
    --accent: #7b3fa6;
  }
  * { margin: 0; padding: 0; box-sizing: border-box; }
  html, body {
    width: 1200px; height: 1138px; overflow: hidden;
    background: var(--backdrop);
    font-family: "Roboto", Arial, sans-serif;
  }
  .canvas { position: relative; width: 1200px; height: 1138px; }

  .card {
    position: absolute;
    border-radius: 16px;
    overflow: hidden;
    box-shadow: 0 6px 14px rgba(0,0,0,0.45);
  }

  /* Front */
  .card-front {
    left: 274px; top: 186px; width: 623px; height: 376px;
    background: linear-gradient(30deg, var(--violet-deep) 0%, var(--violet-mid) 50%, var(--orchid) 100%);
    text-align: center;
  }
  .front-name {
    position: absolute; left: 0; right: 0; top: 148px;
    font-weight: 900; font-size: 40px; letter-spacing: 2px;
    color: #f4f2f6; text-transform: uppercase;
  }
  .front-services {
    position: absolute; left: 0; right: 0; top: 206px;
    font-weight: 500; font-size: 15.5px; letter-spacing: 2.2px;
    color: var(--tag-light); text-transform: uppercase;
  }
  .front-services .divider { margin: 0 9px; }

  /* Back */
  .card-back {
    left: 276px; top: 608px; width: 618px; height: 374px;
    background: linear-gradient(180deg, #f6f6f6 0%, var(--paper) 100%);
  }
  .edge-tab {
    position: absolute; right: 0; top: 44px; width: 15px; height: 60px;
    border-radius: 30px 0 0 30px;
    background: linear-gradient(180deg, var(--orchid), var(--violet-deep));
  }
  .base-band {
    position: absolute; left: 0; right: 0; bottom: 0; height: 10px;
    background: linear-gradient(90deg, var(--orchid), var(--violet-mid), var(--violet-deep));
  }
  .holder { position: absolute; right: 38px; top: 50px; text-align: right; }
  .holder-name {
    font-weight: 900; font-style: italic; font-size: 25px; letter-spacing: 1.5px;
    color: var(--accent); text-transform: uppercase;
  }
  .holder-role { font-size: 16px; color: var(--ink-soft); margin-top: 4px; }

  .brand-block { position: absolute; left: 38px; top: 145px; }
  .brand-dot {
    width: 64px; height: 64px; border-radius: 50%;
    background: var(--accent); margin-left: 40px; margin-bottom: 18px;
  }
  .brand-name {
    font-weight: 900; font-size: 29px; line-height: 30px; letter-spacing: 1px;
    color: var(--ink); text-transform: uppercase;
  }
  .brand-tag {
    font-weight: 500; font-size: 8px; letter-spacing: 0.8px;
    color: var(--accent); text-transform: uppercase; margin-top: 5px;
  }

  .address {
    position: absolute; right: 38px; top: 204px; text-align: right;
    font-size: 15px; line-height: 24px; color: var(--ink-soft);
  }
  .contacts {
    position: absolute; right: 16px; top: 264px; list-style: none;
    font-size: 15px; line-height: 24px; color: var(--ink-soft);
  }
  .contacts li { display: flex; justify-content: flex-end; align-items: center; gap: 12px; }
  .contacts svg { width: 14px; height: 14px; fill: var(--accent); }
  .contacts .hl { color: var(--accent); }
</style>
</head>
<body>
<main class="canvas">

  <section class="card card-front">
    <h1 class="front-name">Stride &amp; Tempo</h1>
    <p class="front-services">Personal Training<span class="divider">|</span>Nutrition<span class="divider">|</span>Motivation</p>
  </section>

  <section class="card card-back">
    <div class="edge-tab"></div>

    <div class="holder">
      <h2 class="holder-name">Marcus Vale</h2>
      <p class="holder-role">Personal Trainer</p>
    </div>

    <div class="brand-block">
      <div class="brand-dot"></div>
      <p class="brand-name">Stride<br>&amp; Tempo</p>
      <p class="brand-tag">Personal training. Nutrition. Motivation</p>
    </div>

    <address class="address" style="font-style:normal">
      1482 Cedar Ridge Lane<br>
      Fairview Texas 75069
    </address>

    <ul class="contacts">
      <li>+1 (555) 214-7730
        <svg viewBox="0 0 16 16" aria-hidden="true"><path d="M2 5c0-2 2-3 6-3s6 1 6 3v1h-3V5H5v1H2z M4 7h8l2 6H2z"/></svg>
      </li>
      <li>marcus@strideandtempo.com
        <svg viewBox="0 0 16 16" aria-hidden="true"><path d="M1 3h14v10H1z M2 4l6 5 6-5" stroke="#fff" stroke-width="1"/></svg>
      </li>
      <li><span>www.<span class="hl">strideandtempo</span>.com</span>
        <svg viewBox="0 0 16 16" aria-hidden="true"><circle cx="8" cy="8" r="7"/><path d="M1 8h14M8 1v14M3 4h10M3 12h10" stroke="#fff" stroke-width="0.9" fill="none"/></svg>
      </li>
    </ul>

    <div class="base-band"></div>
  </section>

</main>
</body>
</html>
```